KVM Contracting services . Building and maintenance services, optic fibre installation

Business cards and logo design.I need a logo that I can use on business cards ,workwear and on my vehicles. I would like the KVM to be the main or larger text and contracting services to be the smaller or less important text.I like monograms, modern designs and repeating patterns symbols. I am also a Gemini and my favourite number is 22 so if this can be any inspiration to help with the design. Am thinking of the using German flag colours as a his is my family’s heritage. And the other 2 main colours I wear is black and white.But any ideas are appreciated.I do not need a design that is trade specific but a design that could be used for any business.

Target Market(s)

General public

Contact Information for Business Card

KVM Contracting Services ( front of business card)

(Back of business card)
Darren Holtwick
0451907326
Maintenance services
Optic fibre and data installation

Logo Text

Logo can just be pattern or monogram or incorporate KVM . I like the gemini star sign and the number 22

Colors
ec1f27
000000
fbee3e
ffffff

Requirements
Must have
• Logo and KVM Contracting Services on the front of business card
Nice to have
• Possible use of German flag colours.
• Modern design.
• Design to be able to be used on black or white background as I want to put it on clothing

```html
<!DOCTYPE html>
<html lang="en">
<head>
<meta charset="utf-8">
<title>KVM Contracting Services – Business Cards</title>
<link rel="stylesheet" href="https://fonts.googleapis.com/css2?family=Open+Sans:wght@400;700&display=swap">
<style>
  :root {
    --backdrop: #3b3431;
    --card: #0b0b0b;
    --red: #ec1f27;
    --white: #ffffff;
    --text-soft: #d8d8d8;
    --silver: #c9c9c9;
    --divider: #3a3a3a;
  }
  * { box-sizing: border-box; margin: 0; padding: 0; }
  html, body {
    width: 1200px;
    height: 844px;
    overflow: hidden;
    background: var(--backdrop);
    font-family: "Open Sans", Arial, sans-serif;
  }
  .scene {
    position: relative;
    width: 1200px;
    height: 844px;
  }
  .card {
    position: absolute;
    top: 279px;
    width: 500px;
    height: 286px;
    background: var(--card);
    box-shadow: 0 10px 24px rgba(0,0,0,0.45);
  }
  .card--details { left: 70px; }
  .card--brand { left: 630px; }

  /* Brand lockup: invented name, one weight, one colour, plain circle */
  .brand {
    position: absolute;
    display: flex;
    align-items: center;
    gap: 14px;
    font-weight: 700;
  }
  .brand__dot {
    width: 46px;
    height: 46px;
    border-radius: 50%;
    flex: none;
  }
  .brand__name {
    display: flex;
    flex-direction: column;
    line-height: 1;
  }
  .brand__mark {
    font-size: 44px;
    letter-spacing: 6px;
  }
  .brand__tagline {
    font-size: 9.5px;
    letter-spacing: 0.6px;
    text-transform: uppercase;
    margin-top: 3px;
  }

  .card--details .brand {
    left: 36px;
    top: 114px;
    color: var(--red);
  }
  .card--details .brand__dot { background: var(--red); }

  .card--brand .brand {
    left: 50%;
    top: 50%;
    transform: translate(-50%, -50%);
    color: var(--silver);
  }
  .card--brand .brand__dot { background: var(--silver); }

  .divider {
    position: absolute;
    left: 246px;
    top: 76px;
    width: 1px;
    height: 118px;
    background: var(--divider);
  }
  .contact {
    position: absolute;
    left: 262px;
    top: 80px;
    color: var(--text-soft);
  }
  .contact__name {
    color: var(--red);
    font-weight: 700;
    font-size: 15px;
    text-transform: uppercase;
    letter-spacing: 0.3px;
  }
  .contact__phone {
    font-size: 14px;
    margin-top: 2px;
  }
  .contact__services {
    list-style: none;
    margin-top: 18px;
    font-size: 14px;
    line-height: 1.3;
  }
</style>
</head>
<body>
  <main class="scene">
    <section class="card card--details" aria-label="Business card back">
      <div class="brand">
        <span class="brand__dot"></span>
        <span class="brand__name">
          <span class="brand__mark">KVM</span>
          <span class="brand__tagline">Contracting Services</span>
        </span>
      </div>
      <span class="divider"></span>
      <div class="contact">
        <p class="contact__name">Darren Holtwick</p>
        <p class="contact__phone">0451907326</p>
        <ul class="contact__services">
          <li>Maintenance services</li>
          <li>Optic fibre and data installation</li>
        </ul>
      </div>
    </section>

    <section class="card card--brand" aria-label="Business card front">
      <div class="brand">
        <span class="brand__dot"></span>
        <span class="brand__name">
          <span class="brand__mark">KVM</span>
          <span class="brand__tagline">Contracting Services</span>
        </span>
      </div>
    </section>
  </main>
</body>
</html>
```